Harborlight Plans (03)

We're designing a website to sell Medicare Supplements. Attached is the script we want to say and general layout, but please use your best knowledge to make it better. This platform should be extremely user-friendly, but we want to make it look fun and approachable! Most Insurance/medicare websites are very boring, drab, simple but we want this one to be more personalized, fun and sexy (but again, still user-friendly since our target demographic is 65+).

This homepage should include a fun and inviting quiz, the script is in the attachment below. It should also include the blurbs about what medicare supplements plans are and why they should buy them. Feel free to play around with cool fonts and imagery, we want the site to be engaging!

Target Market(s)

seniors

Industry/Entity Type

Insurance

Number of Pages Required

1 page

Requirements
Must have
• Quiz, company name and tag line, script
Nice to have
• fun, engaging elements

```html
<!DOCTYPE html>
<html lang="en">
<head>
<meta charset="utf-8">
<title>Harborlight Plans</title>
<link href="https://fonts.googleapis.com/css2?family=Poppins:wght@300;400;500;600&family=Open+Sans:wght@400;600;700&display=swap" rel="stylesheet">
<style>
:root{
  --orange:#f44e2a;
  --ink:#222;
  --text:#333;
  --muted:#555;
  --grey:#f3f3f3;
  --dark:#1e1e1e;
  --dark-line:#555;
  --white:#fff;
}
*{margin:0;padding:0;box-sizing:border-box}
html,body{width:1200px;height:2623px;overflow:hidden;background:var(--white)}
body{position:relative;font-family:"Open Sans",sans-serif;color:var(--text)}
.abs{position:absolute}

/* header */
.brand{left:144px;top:22px;display:flex;align-items:center;gap:12px}
.brand-dot{width:82px;height:82px;border-radius:50%;background:var(--orange)}
.brand-name{font-family:"Poppins",sans-serif;font-size:34px;color:var(--ink);font-weight:400}
.agent{right:145px;top:20px;text-align:right;font-family:"Poppins",sans-serif;padding-right:52px}
.agent small{display:block;font-size:15px;color:var(--ink)}
.agent strong{display:block;font-size:21px;color:var(--orange);font-weight:600;line-height:1.1}
.agent-icon{position:absolute;right:0;top:4px;width:37px;height:37px;border:1.5px solid var(--ink);border-radius:3px;display:flex;align-items:center;justify-content:center}
.nav{right:144px;top:85px;display:flex;gap:32px;font-family:"Poppins",sans-serif;font-size:14px;color:var(--ink)}
.nav .on{color:var(--orange)}

/* hero */
.hero{left:0;top:128px;width:1200px;height:566px;background:linear-gradient(110deg,#5f7a3a 0%,#8fa867 18%,#c9b59a 40%,#9fc3df 60%,#c9a57d 82%,#8a5a3a 100%)}
.hero-cut{left:0;top:600px}
.caption{left:283px;top:455px;width:634px;height:86px;background:rgba(255,255,255,.85);text-align:center;font-family:"Poppins",sans-serif;padding-top:10px}
.caption h1{font-size:34px;font-weight:600;color:var(--orange);line-height:1.1}
.caption p{font-size:16px;color:var(--ink);margin-top:4px}
.dots{left:530px;top:593px;display:flex;gap:20px}
.dots span{width:20px;height:20px;border-radius:50%;background:var(--ink);border:3px solid var(--white)}
.dots .on{background:var(--orange)}

/* welcome */
.welcome{left:0;top:765px;width:1200px;text-align:center}
.welcome h2{font-family:"Poppins",sans-serif;font-size:34px;font-weight:400;color:var(--orange)}
.welcome p{font-size:13.5px;line-height:26px;margin:12px auto 0;width:920px;color:var(--ink)}

/* quiz */
.quiz{left:255px;top:910px;width:691px;height:496px;background:var(--orange)}
.quiz h2{font-family:"Poppins",sans-serif;font-size:58px;font-weight:400;color:var(--white);text-align:center;height:118px;line-height:118px;border-bottom:1px solid #d63c1c}
.field{position:absolute;width:298px}
.field label{display:block;font-family:"Poppins",sans-serif;font-size:21px;color:var(--white);margin-bottom:4px}
.field .box{height:56px;background:var(--white);margin-left:2px;display:flex;align-items:center;justify-content:space-between;padding:0 15px;font-size:16px;color:#555}
.caret{width:0;height:0;border-left:7px solid transparent;border-right:7px solid transparent;border-top:8px solid var(--ink)}
.submit{position:absolute;left:272px;top:398px;width:146px;height:64px;background:var(--dark);color:var(--white);font-family:"Open Sans",sans-serif;font-size:23px;display:flex;align-items:center;justify-content:center;border-radius:2px}

/* info */
.info{left:0;top:1502px;width:1200px;height:758px;background:var(--grey);padding:76px 144px 0}
.info h3{font-family:"Poppins",sans-serif;font-size:19.5px;font-weight:400;color:var(--orange);margin-bottom:12px}
.info p{font-size:13.3px;line-height:25.6px;color:var(--ink)}
.info ul{list-style:none;margin:8px 0 0}
.info li{font-size:13.3px;line-height:25.6px;color:var(--ink);padding-left:12px;position:relative}
.info li::before{content:"•";position:absolute;left:0}
.info .rated li{margin-bottom:8px}
.gap{margin-top:42px}

/* footer */
.footer{left:0;top:2260px;width:1200px;height:363px;background:var(--dark);color:#bbb}
.footer h4{font-family:"Poppins",sans-serif;font-size:21px;font-weight:400;color:var(--white)}
.col{position:absolute;top:40px}
.col small{display:block;font-size:10px;margin-top:14px}
.email{width:243px;height:40px;background:var(--white);margin-top:8px;font-size:12px;color:#666;padding:12px 15px}
.sub{display:inline-block;margin-top:9px;background:var(--orange);color:var(--white);font-size:12px;padding:10px 14px}
.contact{margin-top:14px;font-size:11.5px;line-height:32px}
.contact div{display:flex;align-items:center;gap:16px}
.socials{display:flex;gap:16px;margin-top:20px}
.socials span{width:40px;height:40px;border-radius:50%;border:1px solid #888}
.rule{left:144px;top:2495px;width:912px;height:1px;background:var(--dark-line)}
.links{left:144px;top:2540px;font-size:11.5px}
.copy{left:144px;top:2576px;font-size:11.5px}
.top-btn{left:1016px;top:2546px;width:38px;height:38px;border-radius:50%;background:#777;display:flex;align-items:center;justify-content:center}
</style>
</head>
<body>

<header>
  <div class="abs brand"><span class="brand-dot"></span><span class="brand-name">Harborlight Plans</span></div>
  <div class="abs agent">
    <small>Talk to a live agent</small>
    <strong>(800) 555-0142</strong>
    <span class="agent-icon"><svg width="18" height="18" viewBox="0 0 24 24"><path fill="#222" d="M6.6 10.8c1.4 2.8 3.8 5.1 6.6 6.6l2.2-2.2c.3-.3.7-.4 1-.2 1.1.4 2.3.6 3.6.6.6 0 1 .4 1 1V20c0 .6-.4 1-1 1C10.6 21 3 13.4 3 4c0-.6.4-1 1-1h3.5c.6 0 1 .4 1 1 0 1.3.2 2.5.6 3.6.1.3 0 .7-.2 1z"/></svg></span>
  </div>
  <nav class="abs nav"><span class="on">MEDICARE</span><span>SUPPLEMTS</span><span>POLICIES</span><span>ABOUT</span><span>SUPPORT</span></nav>
</header>

<section>
  <div class="abs hero" role="img" aria-label="Photo of a smiling senior couple looking at a laptop at home"></div>
  <svg class="abs hero-cut" width="1200" height="95" viewBox="0 0 1200 95">
    <polygon points="600,55 1200,88 1200,95 0,95 0,93" fill="#fff"/>
    <polygon points="0,15 600,55 0,93" fill="#2b2b2b"/>
  </svg>
  <div class="abs caption">
    <h1>Harborlight Plans</h1>
    <p>Be confident in choosing the Medicare Supplement plan that's right for you.</p>
  </div>
  <div class="abs dots"><span class="on"></span><span></span><span></span><span></span></div>
</section>

<section class="abs welcome">
  <h2>Welcome</h2>
  <p>We know insurance can be confusing. With so much information and not enough answers, we're here to help you find the plan that works best for you, your family and your health. Take this short quiz to find flexible and affordable plans that you can feel confident in.</p>
</section>

<section class="abs quiz">
  <h2>Quiz</h2>
  <div class="field" style="left:21px;top:144px"><label>I am :</label><div class="box">Over 64 years old<span class="caret"></span></div></div>
  <div class="field" style="left:367px;top:144px"><label>I am :</label><div class="box">Male<span class="caret"></span></div></div>
  <div class="field" style="left:21px;top:265px"><label>I want to see :</label><div class="box">Free plans<span class="caret"></span></div></div>
  <div class="field" style="left:367px;top:265px"><label>Enter zip code :</label><div class="box">Zip code<svg width="14" height="20" viewBox="0 0 14 20"><path fill="#222" d="M7 0C3.1 0 0 3.1 0 7c0 5 7 13 7 13s7-8 7-13c0-3.9-3.1-7-7-7zm0 10a3 3 0 110-6 3 3 0 010 6z"/></svg></div></div>
  <div class="submit">SUBMIT</div>
</section>

<section class="abs info">
  <h3>What is a Medicare Supplement plan?</h3>
  <p>Each Medicare Supplement insurance plan offers a different level of basic benefits, but each lettered plan will include the same standardized basic bene-fits regardless of insurance company and location. Medicare Supplement insurance plans do not always cover vision, dental, long-term care, or hearing aids, but all plans must cover at least a portion of the following basic benefits:</p>
  <ul>
    <li>Medicare Part A coinsurance costs up to an additional 365 days after Medicare benefits are exhausted</li>
    <li>Medicare Part A hospice care coinsurance or copayments</li>
    <li>Medicare Part B coinsurance or copayments</li>
    <li>First three pints of blood used in a medical procedure</li>
  </ul>
  <h3 class="gap">Medicare Supplement insurance plan costs</h3>
  <p>Although private insurance companies are required to offer the same basic benefits for each lettered plan, they do have the ability to charge different premiums. You might want to shop around to find a Medicare Supplement insurance plan that may fit your medical and financial needs. Insurance com-panies may price their plan premiums in any of the following ways:</p>
  <ul class="rated">
    <li><b>Community no-age-rated:</b> These Medicare Supplement insurance plans charge premiums that are the same across the board, regardless of age.</li>
    <li><b>Issue-age-rated:</b> These plans base their premiums on your age when you first enrolled in the policy. Therefore, the younger you are when you enroll in this type of plan, the lower your premium will be.</li>
    <li><b>Attained-age-rated:</b> Like issue-age-rated, these plans base their premiums on the age you were when you first bought a policy, but unlike issue-age-rated, premiums increase as you get older.</li>
  </ul>
  <p style="margin-top:18px">Please note that no matter what rating method an insurance company uses, premiums may increase over time for reasons other than age, such as inflation.</p>
</section>

<footer class="abs footer">
  <div class="col" style="left:144px">
    <h4>Stay in touch</h4>
    <small>Vestibulum condimentum, risus ut posuere cursus</small>
    <div class="email">Email Address</div>
    <span class="sub">SUBSCRIBE</span>
  </div>
  <div class="col" style="left:473px">
    <h4>Stay in the loop?</h4>
    <div class="contact">
      <div><svg width="8" height="11" viewBox="0 0 14 20"><path fill="#999" d="M7 0C3.1 0 0 3.1 0 7c0 5 7 13 7 13s7-8 7-13c0-3.9-3.1-7-7-7z"/></svg>24 Building name, Street name, City Zipcode</div>
      <div><svg width="10" height="10" viewBox="0 0 24 24"><path fill="#999" d="M6.6 10.8c1.4 2.8 3.8 5.1 6.6 6.6l2.2-2.2c.3-.3.7-.4 1-.2 1.1.4 2.3.6 3.6.6.6 0 1 .4 1 1V20c0 .6-.4 1-1 1C10.6 21 3 13.4 3 4c0-.6.4-1 1-1h3.5c.6 0 1 .4 1 1 0 1.3.2 2.5.6 3.6.1.3 0 .7-.2 1z"/></svg>(800) 555-0142</div>
      <div><svg width="10" height="8" viewBox="0 0 10 8"><rect width="10" height="8" fill="#999"/><path d="M0 0l5 4 5-4" stroke="#1e1e1e" fill="none"/></svg>hello@harborlightplans.com</div>
    </div>
  </div>
  <div class="col" style="left:788px">
    <h4>Follow us on</h4>
    <div class="socials"><span></span><span></span><span></span><span></span><span></span></div>
  </div>
</footer>
<div class="abs rule"></div>
<div class="abs links" style="color:#bbb">Home &nbsp;|&nbsp; Medicare &nbsp;|&nbsp; Supplemts &nbsp;|&nbsp; Policies &nbsp;|&nbsp; About &nbsp;|&nbsp; Support</div>
<div class="abs copy" style="color:#bbb">Copyright © 2020 Harborlight Plans. &nbsp;All rights reserved.</div>
<div class="abs top-btn"><svg width="20" height="12" viewBox="0 0 20 12"><path d="M2 10l8-8 8 8" stroke="#1e1e1e" stroke-width="3" fill="none"/></svg></div>

</body>
</html>
```